BUSINESS CARD DESIGN

NAME- DALE VORSKIN
PHONE NUMER - 555- 714-9082
EMAIL- OFFICE@TRV-GROUNDMAKRZ.COM
BACK OF CARD- SPEACIALIZES IN LAND CLEARING, FORESTRY MUCLHING AND EXCAVATION

Contact Information for Business Card

NAME- DALE VORSKIN PHONE NUMER - 555- 714-9082 EMAIL- OFFICE@TRV-GROUNDMAKRZ.COM BACK OF CARD- SPEACIALIZES IN LAND CLEARING , MUCLHING AND EXCAVATION

```html
<!DOCTYPE html>
<html lang="en">
<head>
<meta charset="utf-8">
<title>Traverse Groundmakrz – Business Card</title>
<link href="https://fonts.googleapis.com/css2?family=Roboto:wght@300;400;700&display=swap" rel="stylesheet">
<style>
  :root {
    --bg: #e3e7e8;
    --card: #202024;
    --accent: #f6b219;
    --emboss: #17171a;
    --text-light: #ffffff;
  }
  * { margin: 0; padding: 0; box-sizing: border-box; }
  html, body { width: 1200px; height: 960px; overflow: hidden; }
  body {
    background: var(--bg);
    font-family: 'Roboto', sans-serif;
    position: relative;
  }
  .card {
    position: absolute;
    left: 250px;
    width: 702px;
    height: 400px;
    background: var(--card);
  }
  .card--front { top: 60px; }
  .card--back { top: 500px; }
  .edge-bar {
    position: absolute;
    top: 100px;
    width: 16px;
    height: 200px;
    background: var(--accent);
  }
  .edge-bar--left { left: 0; }
  .edge-bar--right { right: 0; }

  .brand {
    position: absolute;
    display: flex;
    flex-direction: column;
    align-items: center;
    font-weight: 700;
    text-align: center;
  }
  .brand__mark { border-radius: 50%; }
  .brand__name {
    letter-spacing: 2px;
    line-height: 1.25;
  }

  .card--front .brand {
    left: 0; right: 0; top: 78px;
    color: var(--emboss);
  }
  .card--front .brand__mark {
    width: 150px; height: 150px;
    background: var(--emboss);
    margin-bottom: 20px;
  }
  .card--front .brand__name { font-size: 26px; }

  .tagline {
    position: absolute;
    left: 0; right: 0; top: 355px;
    text-align: center;
    color: var(--accent);
    font-size: 15.5px;
    letter-spacing: 0.6px;
  }

  .card--back .brand {
    left: 60px; width: 232px; top: 108px;
    color: var(--accent);
  }
  .card--back .brand__mark {
    width: 110px; height: 110px;
    background: var(--accent);
    margin-bottom: 16px;
  }
  .card--back .brand__name { font-size: 19px; }

  .divider {
    position: absolute;
    left: 351px; top: 94px;
    width: 1px; height: 212px;
    background: var(--accent);
    opacity: 0.7;
  }
  .contact {
    position: absolute;
    left: 395px; top: 140px;
    width: 285px;
  }
  .contact__name {
    font-size: 37px;
    color: var(--accent);
    letter-spacing: 1px;
    line-height: 1;
    margin-bottom: 24px;
    white-space: nowrap;
  }
  .contact__first { font-weight: 700; }
  .contact__last { font-weight: 300; }
  .contact__row {
    display: flex;
    align-items: center;
    gap: 10px;
    color: var(--text-light);
    font-size: 15px;
    letter-spacing: 0.2px;
    margin-bottom: 8px;
    white-space: nowrap;
  }
  .contact__icon { width: 16px; height: 16px; flex: none; }
  .website {
    position: absolute;
    left: 0; right: 0; top: 354px;
    text-align: center;
    color: var(--accent);
    font-size: 16px;
    letter-spacing: 0.6px;
  }
</style>
</head>
<body>
  <section class="card card--front">
    <div class="edge-bar edge-bar--left"></div>
    <div class="edge-bar edge-bar--right"></div>
    <div class="brand">
      <div class="brand__mark"></div>
      <div class="brand__name">TRAVERSE GROUNDMAKRZ LLC<br>555-714-9082</div>
    </div>
    <p class="tagline">SPEACIALIZES IN LAND CLEARING , MUCLHING AND EXCAVATION</p>
  </section>

  <section class="card card--back">
    <div class="edge-bar edge-bar--left"></div>
    <div class="edge-bar edge-bar--right"></div>
    <div class="brand">
      <div class="brand__mark"></div>
      <div class="brand__name">TRAVERSE<br>GROUNDMAKRZ LLC<br>555-714-9082</div>
    </div>
    <div class="divider"></div>
    <div class="contact">
      <h1 class="contact__name"><span class="contact__first">DALE</span> <span class="contact__last">VORSKIN</span></h1>
      <div class="contact__row">
        <svg class="contact__icon" viewBox="0 0 24 24" aria-hidden="true">
          <path fill="#f6b219" d="M6.6 10.8c1.4 2.8 3.8 5.1 6.6 6.6l2.2-2.2c.3-.3.7-.4 1-.2 1.1.4 2.3.6 3.6.6.6 0 1 .4 1 1V20c0 .6-.4 1-1 1C10.6 21 3 13.4 3 4c0-.6.4-1 1-1h3.5c.6 0 1 .4 1 1 0 1.3.2 2.5.6 3.6.1.3 0 .7-.2 1L6.6 10.8z"/>
        </svg>
        <span>555- 714-9082</span>
      </div>
      <div class="contact__row">
        <svg class="contact__icon" viewBox="0 0 24 24" aria-hidden="true">
          <path fill="#f6b219" d="M2 9l10-7 10 7v12H2V9zm2 1.5V19h16v-8.5l-8 5.5-8-5.5z"/>
        </svg>
        <span>OFFICE@TRV-GROUNDMAKRZ.COM</span>
      </div>
    </div>
    <p class="website">WWW.TRV-GROUNDMAKRZ.COM</p>
  </section>
</body>
</html>
```